VTMB site redesign

Please redesign a home page with content provided. PSD only - no coding
Can use any images from Snapwelder.com

Please create a site design that more clearly illustrates the client's services and expertise. We are looking for a high-end design.

Any images used must be generic or of Dallas TX.

Fonts: Any
Colors: Match to logo
Look: Modern - Professional

Target Market(s)

medium-large business owners

Number of Pages Required

1 page

Font styles to use
Serif
Sans Serif

Requirements
Must have
• cohesive professional design
• high end look
• Match to logo

```html
<!DOCTYPE html>
<html lang="en">
<head>
<meta charset="utf-8">
<title>VTMB – Office and Warehouse Tenant Representation</title>
<link rel="stylesheet" href="https://fonts.googleapis.com/css2?family=Libre+Baskerville:ital,wght@0,400;0,700;1,400&family=Lato:ital,wght@0,400;0,700;0,900;1,400&display=swap">
<style>
:root{
  --red:#d2322d;
  --red-soft:#df524c;
  --navy:#262a37;
  --navy-deep:#1f2330;
  --ink:#222;
  --grey:#555;
  --pale:#f1f1f1;
  --white:#fff;
  --serif:"Libre Baskerville", Georgia, serif;
  --sans:"Lato", Arial, sans-serif;
}
*{margin:0;padding:0;box-sizing:border-box}
html,body{width:1200px;height:3249px;overflow:hidden}
body{position:relative;background:var(--white);font-family:var(--sans);color:var(--ink)}
.abs{position:absolute}

/* header */
.header-shape{position:absolute;left:0;top:0;width:1200px;height:140px;z-index:3}
.brand{position:absolute;left:121px;top:34px;z-index:4;display:flex;align-items:center;gap:12px}
.brand-mark{width:22px;height:22px;background:var(--white)}
.brand-name{font-family:var(--serif);font-weight:700;font-size:40px;color:var(--white);letter-spacing:2px}
.call{position:absolute;left:808px;top:26px;z-index:4;display:flex;align-items:center;gap:16px;color:var(--white);font-family:var(--serif);font-size:19px}
.call-icon{width:36px;height:36px;background:var(--white);display:flex;align-items:center;justify-content:center}
.call b{font-weight:700}
.nav{position:absolute;left:357px;top:86px;width:843px;height:38px;background:var(--navy-deep);z-index:4;display:flex}
.nav a{color:var(--white);text-decoration:none;font-size:12px;letter-spacing:.3px;display:flex;align-items:center;padding:0 28px;border-right:1px solid #4a4f5d}
.nav a.active{font-weight:700;padding:0 32px}

/* hero */
.hero{position:absolute;left:0;top:124px;width:1200px;height:489px;background:linear-gradient(100deg,#3b3d40 0%,#8a8f95 25%,#c9ccd0 55%,#e7e4df 80%,#b7b4ae 100%)}
.hero-text{position:absolute;right:140px;top:170px;width:420px;text-align:right;color:var(--white);z-index:2}
.hero-text h1{font-size:31px;font-weight:700;line-height:44px;text-transform:uppercase}
.hero-text p{font-size:17px;line-height:25px;margin-top:10px}
.hero-arrow{position:absolute;top:345px;z-index:2}

/* section titles */
.title{position:absolute;left:0;width:1200px;text-align:center;font-family:var(--serif);font-weight:700;font-size:28px;color:var(--ink);letter-spacing:.5px}
.title span{color:var(--red)}
.rule{position:absolute;left:50%;transform:translateX(-50%);height:2px;background:#cfcfcf}
.rule::after{content:"";position:absolute;left:50%;top:0;transform:translateX(-50%);width:44px;height:3px;background:var(--ink)}

.btn{position:absolute;display:flex;align-items:center;justify-content:center;font-size:12px;font-weight:700;color:var(--white);text-transform:uppercase}
.btn-red{background:var(--red)}
.btn-navy{background:var(--navy)}

/* about */
.about-lead{position:absolute;left:0;width:1200px;top:752px;text-align:center;font-size:14px;font-weight:700}
.about-copy{position:absolute;left:160px;width:880px;top:785px;text-align:center;font-size:11.5px;line-height:22px;color:#333}

/* why */
.why{position:absolute;left:0;top:964px;width:1200px;height:448px;background:linear-gradient(135deg,#f6f6f6 0%,#e9eaec 40%,#f8f8f8 70%,#e4e5e7 100%)}
.feature{position:absolute;width:220px;text-align:center}
.feature-ring{width:120px;height:120px;border-radius:50%;background:var(--white);margin:0 auto;display:flex;align-items:center;justify-content:center;box-shadow:0 0 0 1px #ddd}
.feature-dot{width:104px;height:104px;border-radius:50%;background:var(--navy);display:flex;align-items:center;justify-content:center}
.feature-dot.red{background:var(--red)}
.feature h3{font-size:14px;font-weight:400;margin-top:28px;color:var(--ink)}
.feature h3.red{color:var(--red)}
.feature p{font-size:11px;line-height:16px;color:#444;margin-top:6px;padding:0 20px}
.feature .more{font-size:10px;font-weight:700;color:var(--red);margin-top:6px;letter-spacing:.5px}
.feature .more.dark{color:var(--ink)}

/* cta band */
.cta{position:absolute;left:0;top:1412px;width:1200px;height:228px;background:var(--red-soft)}
.cta p{position:absolute;left:0;width:1200px;top:44px;text-align:center;color:var(--white);font-size:23px;line-height:34px;font-weight:700}

/* team */
.team-copy{position:absolute;left:130px;width:940px;top:1776px;text-align:center;font-size:12px;line-height:22px;color:#333}
.avatar{position:absolute;border-radius:50%}
.bio-line{position:absolute;left:454px;top:2146px;width:2px;height:194px;background:var(--red)}
.social-dot{position:absolute;left:441px;width:28px;height:28px;border-radius:50%;background:var(--white);border:1.5px solid var(--red);display:flex;align-items:center;justify-content:center}
.bio-name{position:absolute;left:504px;top:2140px;font-family:var(--serif);font-size:18px;color:var(--ink)}
.bio-role{position:absolute;left:504px;top:2168px;font-family:var(--serif);font-style:italic;font-size:13px;color:#777}
.bio-copy{position:absolute;left:504px;top:2196px;width:586px;font-size:13px;line-height:23px;color:#333;text-align:justify}
.team-brand{position:absolute;left:210px;top:2208px;display:flex;align-items:center;gap:10px}
.team-brand .brand-mark{background:var(--red)}
.team-brand .brand-name{color:var(--red);font-size:36px}

/* news */
.news{position:absolute;left:0;top:2394px;width:1200px;height:374px;background:var(--pale)}
.col-title{position:absolute;font-family:var(--serif);font-weight:700;font-size:23px;color:var(--ink)}
.col-title span{color:var(--red)}
.pager{position:absolute;display:flex;gap:4px}
.pager i{width:20px;height:20px;border:1.5px solid #555;display:flex;align-items:center;justify-content:center}
.pager i.on{border-color:var(--red)}
.col-rule{position:absolute;height:1px;background:#cfcfcf}
.post{position:absolute;left:121px;width:440px}
.post-date{position:absolute;left:0;top:0;width:46px;text-align:center}
.post-date .d{background:var(--navy);color:var(--white);font-size:18px;height:27px;line-height:27px}
.post-date .m{background:var(--red);color:var(--white);font-size:10px;font-weight:700;height:17px;line-height:17px}
.post h4{position:absolute;left:60px;top:0;font-size:14px;font-weight:700;color:var(--ink);white-space:nowrap}
.post p{position:absolute;left:60px;top:24px;width:380px;font-size:11px;line-height:17px;color:#333}
.quote{position:absolute;left:624px;top:2540px;width:460px;font-size:11.5px;line-height:23px;font-style:italic;color:#333}
.quote-by{position:absolute;left:622px;top:2694px;font-family:var(--serif);font-style:italic;font-size:14px;color:var(--red)}
.divider-v{position:absolute;left:600px;top:2470px;width:1px;height:250px;background:#d0d0d0}

/* footer */
.footer{position:absolute;left:0;top:2768px;width:1200px;height:433px;background:var(--navy)}
.f-head{position:absolute;top:2818px;font-family:var(--serif);font-weight:700;font-size:14px;color:var(--white);text-transform:uppercase}
.f-rule{position:absolute;top:2844px;height:1px;background:#4b5060}
.f-links{position:absolute;left:125px;top:2858px;list-style:none;color:var(--white);font-size:11.5px;line-height:26px}
.f-links li::before{content:"• ";}
.f-contact{position:absolute;left:294px;top:2858px;color:var(--white);font-size:12px;line-height:20px}
.f-row{position:absolute;left:294px;display:flex;align-items:center;gap:12px;color:var(--white);font-size:12px}
.map{position:absolute;left:560px;top:2866px;width:262px;height:150px;background:linear-gradient(135deg,#e8e6e1,#d7dde3 60%,#eae7df)}
.foot-brand{position:absolute;left:905px;top:2866px;display:flex;align-items:center;gap:10px}
.foot-brand .brand-mark{background:#d9d9dc}
.foot-brand .brand-name{color:#e9e9ec;font-size:36px}
.f-sep{position:absolute;left:121px;top:3048px;width:958px;height:1px;background:#3f4452}
.notices{position:absolute;left:0;width:1200px;top:3076px;text-align:center;color:var(--white);font-size:12.5px;line-height:30px}
.notices .u{text-decoration:underline}
.copyright{position:absolute;left:0;top:3201px;width:1200px;height:48px;background:var(--red)}
.copyright p{position:absolute;left:121px;top:16px;color:var(--white);font-size:11px}
.socials{position:absolute;right:120px;top:12px;display:flex;gap:6px}
.socials i{width:24px;height:24px;border-radius:50%;background:#2f5fb3;border:1.5px solid var(--white)}
</style>
</head>
<body>

<!-- header -->
<svg class="header-shape" viewBox="0 0 1200 140" aria-hidden="true">
  <polygon points="0,0 1200,0 1200,86 357,86 330,140 0,140" fill="#d2322d"/>
</svg>
<div class="brand"><div class="brand-mark"></div><div class="brand-name">VTMB</div></div>
<div class="call">
  <div class="call-icon">
    <svg width="20" height="20" viewBox="0 0 24 24"><path d="M6.6 10.8a15 15 0 0 0 6.6 6.6l2.2-2.2a1 1 0 0 1 1-.25 11.4 11.4 0 0 0 3.6.57 1 1 0 0 1 1 1V20a1 1 0 0 1-1 1A17 17 0 0 1 3 4a1 1 0 0 1 1-1h3.5a1 1 0 0 1 1 1c0 1.25.2 2.45.57 3.6a1 1 0 0 1-.25 1z" fill="#d2322d"/></svg>
  </div>
  <span>Call Today: <b>555-410-2626</b></span>
</div>
<nav class="nav">
  <a class="active">HOME</a><a>ABOUT VTMB</a><a>SERVICES</a><a style="padding:0 44px">BLOG</a><a style="padding:0 36px">MARKET NEWS</a><a style="padding:0 44px">CONTACT US</a>
</nav>

<!-- hero -->
<div class="hero" role="img" aria-label="Photo of a broker in a blue shirt talking with a client across a desk in a bright office"></div>
<svg class="hero-arrow" style="left:92px" width="24" height="46" viewBox="0 0 24 46"><polyline points="22,2 2,23 22,44" fill="none" stroke="#fff" stroke-width="2"/></svg>
<svg class="hero-arrow" style="left:1082px" width="24" height="46" viewBox="0 0 24 46"><polyline points="2,2 22,23 2,44" fill="none" stroke="#fff" stroke-width="2"/></svg>
<div class="hero-text" style="top:300px">
  <h1>Professional Office and Warehouse Leasing</h1>
  <p>Fast-track your search with tenant reps that only serve you, and specialize in the DFW area.</p>
</div>

<!-- about -->
<h2 class="title" style="top:668px">ABOUT <span>VTMB</span></h2>
<div class="rule" style="top:711px;width:200px"></div>
<p class="about-lead">Ut enim ad minim veniam, quis nostrud exercitation ullamco laboris nisi ut aliquip ex ea commodo consequat.</p>
<p class="about-copy">Lorem ipsum dolor sit amet, consectetur adipiscing elit, sed do eiusmod tempor incididunt ut labore et dolore magna aliqua. Ut enim ad minim veniam, quis nostrud exercitation ullamco laboris nisi ut aliquip ex ea commodo consequat. Duis aute irure dolor in reprehenderit in voluptate velit esse cillum dolore eu fugiat nulla pariatur. Excepteur sint occaecat cupidatat non proident, sunt in culpa qui officia deserunt mollit anim id est laborum</p>
<div class="btn btn-red" style="left:544px;top:866px;width:112px;height:36px">Read More</div>

<!-- why tenant representation -->
<div class="why" role="img" aria-label="Faint photo of a modern glass office building facade"></div>
<h2 class="title" style="top:1016px">WHY TENANT <span>REPRESENTATION?</span></h2>
<div class="rule" style="top:1072px;width:504px"></div>

<div class="feature" style="left:109px;top:1122px">
  <div class="feature-ring"><div class="feature-dot red">
    <svg width="40" height="40" viewBox="0 0 40 40" fill="#fff"><circle cx="12" cy="12" r="5"/><circle cx="28" cy="12" r="5"/><path d="M4 30c0-6 4-10 8-10s8 4 8 10zM20 30c0-6 4-10 8-10s8 4 8 10z"/></svg>
  </div></div>
  <h3 class="red">Relationships</h3>
  <p>Save time by trusting VTMB year after year to find the right location for</p>
  <div class="more">READ MORE ▸</div>
</div>
<div class="feature" style="left:375px;top:1122px">
  <div class="feature-ring"><div class="feature-dot">
    <svg width="40" height="40" viewBox="0 0 40 40" fill="none" stroke="#fff" stroke-width="2.5"><rect x="9" y="18" width="22" height="16" rx="2"/><path d="M14 18v-5a6 6 0 0 1 12 0v5"/></svg>
  </div></div>
  <h3>Access To More</h3>
  <p>We have no agreements or personal incentives for specific properties</p>
  <div class="more dark">READ MORE ▸</div>
</div>
<div class="feature" style="left:626px;top:1122px">
  <div class="feature-ring"><div class="feature-dot">
    <svg width="40" height="40" viewBox="0 0 40 40" fill="#fff"><circle cx="20" cy="13" r="7"/><path d="M6 36c0-9 6-14 14-14s14 5 14 14z"/></svg>
  </div></div>
  <h3>Free To You</h3>
  <p>You pay us nothing. We get our commission from the property</p>
  <div class="more dark">READ MORE ▸</div>
</div>
<div class="feature" style="left:873px;top:1122px">
  <div class="feature-ring"><div class="feature-dot">
    <svg width="40" height="40" viewBox="0 0 40 40" fill="#fff"><circle cx="22" cy="10" r="5"/><path d="M4 26h8l8 4h8l8-6v4l-8 7H18l-8-3H4z"/></svg>
  </div></div>
  <h3>Customized Service</h3>
  <p>Aside from saving you the time of repeating what you needs</p>
  <div class="more dark">READ MORE ▸</div>
</div>

<!-- call to action -->
<div class="cta">
  <p>If you need to find office or warehouse space in the Dallas Fort Worth<br>area, the team at VTMB has the experience you need.</p>
</div>
<div class="btn btn-navy" style="left:524px;top:1546px;width:152px;height:38px;font-weight:400">Space Calculator</div>

<!-- team -->
<h2 class="title" style="top:1692px">MEET <span>THE TEAM</span></h2>
<div class="rule" style="top:1738px;width:276px"></div>
<p class="team-copy">At VTMB we believe that you deserve the best professional advice and personal service with your commercial real estate negotiations. By choosing VTMB as your tenant reps in the Dallas/Fort Worth area, you will receive the assistance of accomplished and experienced commercial real estate brokers and salespeople who are licensed by the State Realty Licensing Board to practice in Texas since 1982.</p>

<svg class="abs" style="left:379px;top:1914px" width="152" height="172" viewBox="0 0 152 172" aria-hidden="true">
  <path d="M76 4a72 72 0 0 1 14 142.6L76 168 62 146.6A72 72 0 0 1 76 4z" fill="#d2322d"/>
</svg>
<div class="avatar" style="left:391px;top:1926px;width:128px;height:128px;background:linear-gradient(160deg,#6f7c86,#c88a4a)" role="img" aria-label="Portrait of a smiling team member in a safety vest"></div>
<div class="avatar" style="left:563px;top:1932px;width:112px;height:112px;background:linear-gradient(160deg,#d8dde4,#7d6a5d)" role="img" aria-label="Portrait of a smiling team member"></div>
<div class="avatar" style="left:704px;top:1932px;width:112px;height:112px;background:linear-gradient(160deg,#cfd6df,#3b4a7a)" role="img" aria-label="Portrait of a smiling team member"></div>

<div class="team-brand"><div class="brand-mark"></div><div class="brand-name">VTMB</div></div>
<div class="bio-line"></div>
<div class="social-dot" style="top:2206px"><svg width="12" height="12" viewBox="0 0 12 12"><circle cx="6" cy="6" r="3" fill="#d2322d"/></svg></div>
<div class="social-dot" style="top:2245px"><svg width="12" height="12" viewBox="0 0 12 12"><circle cx="6" cy="6" r="3" fill="#d2322d"/></svg></div>
<div class="bio-name">Marcus D. Verlane</div>
<div class="bio-role">Founder and President</div>
<p class="bio-copy">Lorem ipsum dolor sit amet, consectetuer adipiscing elit, sed diam nonummy nibh euismod tincidunt ut laoreet dolore magna aliquam erat volutpat. Ut wisi enim ad minim veniam, quis nostrud exerci tation ullamcorper suscipit lobortis nisl ut aliquip ex ea commodo consequat. Duis autem vel eum iriure dolor in hendrerit in vulputate velit esse molestie consequat, vel illum dolore eu feugiat nulla facilisis at vero eros et accumsan et iusto odio dignissim qui blandit praesent luptatum zzril delenit augue duis dolore te feugait nulla facilisi</p>

<!-- articles and testimonials -->
<div class="news"></div>
<h3 class="col-title" style="left:121px;top:2450px">RECENT <span>ARTICLES</span></h3>
<div class="pager" style="left:528px;top:2452px"><i class="on"><svg width="8" height="10" viewBox="0 0 8 10"><polyline points="6,1 2,5 6,9" fill="none" stroke="#d2322d" stroke-width="1.5"/></svg></i><i><svg width="8" height="10" viewBox="0 0 8 10"><polyline points="2,1 6,5 2,9" fill="none" stroke="#333" stroke-width="1.5"/></svg></i></div>
<div class="col-rule" style="left:121px;top:2488px;width:456px"></div>
<div class="post" style="top:2540px">
  <div class="post-date"><div class="d">08</div><div class="m">MAY</div></div>
  <h4>Diam Nonummy Nibh Euism Od Tincidunt</h4>
  <p>Lorem ipsum dolor sit amet, consectetuer adipiscing elit, sedi dia nummy nibh euism od tincidunt ut laoreet doloremoi magna aliquam</p>
</div>
<div class="col-rule" style="left:121px;top:2630px;width:456px;background:#dcdcdc"></div>
<div class="post" style="top:2650px">
  <div class="post-date"><div class="d">08</div><div class="m">MAY</div></div>
  <h4>Diam Nonummy Nibh Euism Od Tincidunt</h4>
  <p>Lorem ipsum dolor sit amet, consectetuer adipiscing elit, sedi dia nummy nibh euism od tincidunt ut laoreet doloremoi magna aliquam</p>
</div>

<div class="divider-v"></div>
<h3 class="col-title" style="left:622px;top:2450px">CLIENT <span>TESTIMONIALS</span></h3>
<div class="pager" style="left:1030px;top:2452px"><i class="on"><svg width="8" height="10" viewBox="0 0 8 10"><polyline points="6,1 2,5 6,9" fill="none" stroke="#d2322d" stroke-width="1.5"/></svg></i><i><svg width="8" height="10" viewBox="0 0 8 10"><polyline points="2,1 6,5 2,9" fill="none" stroke="#333" stroke-width="1.5"/></svg></i></div>
<div class="col-rule" style="left:622px;top:2488px;width:456px"></div>
<svg class="abs" style="left:622px;top:2546px" width="18" height="14" viewBox="0 0 18 14"><path d="M0 14V8C0 3 2 1 6 0v3C4 4 3 5 3 7h4v7zM10 14V8c0-5 2-7 6-8v3c-2 1-3 2-3 4h4v7z" fill="#999"/></svg>
<p class="quote">&nbsp;&nbsp;&nbsp;&nbsp;&nbsp;The real estate team at VTMB has decades of experience in Commercial. One advantage of VTMB is they know all the properties that are about to become available, BEFORE they are available. They have the inside track on properties and they watch your back at the negotiating table. Very impressive with a polished approach. Let the team run with your next project and you won't be disappointed</p>
<p class="quote-by">~ Nathan Ellis Ward</p>

<!-- footer -->
<div class="footer"></div>
<div class="f-head" style="left:122px">Quick Links</div>
<div class="f-rule" style="left:122px;width:122px"></div>
<ul class="f-links"><li>Home</li><li>About Vtmb</li><li>Services</li><li>Blog</li><li>Market News</li><li>Contact Us</li></ul>

<div class="f-head" style="left:294px">Contact Information</div>
<div class="f-rule" style="left:294px;width:226px"></div>
<p class="f-contact">412 Cedar Brook Avenue, Suite 850,<br>Dallas, TX 75219</p>
<div class="f-row" style="top:2920px"><svg width="12" height="12" viewBox="0 0 24 24"><path d="M6.6 10.8a15 15 0 0 0 6.6 6.6l2.2-2.2a1 1 0 0 1 1-.25 11.4 11.4 0 0 0 3.6.57 1 1 0 0 1 1 1V20a1 1 0 0 1-1 1A17 17 0 0 1 3 4a1 1 0 0 1 1-1h3.5a1 1 0 0 1 1 1c0 1.25.2 2.45.57 3.6a1 1 0 0 1-.25 1z" fill="#fff"/></svg>555-410-2626</div>
<div class="f-row" style="top:2956px"><svg width="12" height="12" viewBox="0 0 12 12"><rect x="1" y="4" width="10" height="6" fill="none" stroke="#fff" stroke-width="1.3"/><rect x="3" y="1" width="6" height="3" fill="#fff"/></svg>555-410-3299</div>
<div class="f-row" style="top:2992px"><svg width="12" height="10" viewBox="0 0 12 10"><rect x=".7" y=".7" width="10.6" height="8.6" fill="none" stroke="#fff" stroke-width="1.3"/><polyline points="1,1 6,5.5 11,1" fill="none" stroke="#fff" stroke-width="1.3"/></svg>info@vtmb.com</div>

<div class="f-head" style="left:560px">Location Map</div>
<div class="f-rule" style="left:560px;width:262px"></div>
<div class="map" role="img" aria-label="Street map of the office location in Dallas"></div>
<svg class="abs" style="left:684px;top:2920px" width="16" height="22" viewBox="0 0 16 22"><path d="M8 0a8 8 0 0 1 8 8c0 6-8 14-8 14S0 14 0 8a8 8 0 0 1 8-8z" fill="#d2322d"/><circle cx="8" cy="8" r="3" fill="#fff"/></svg>

<div class="foot-brand"><div class="brand-mark"></div><div class="brand-name">VTMB</div></div>

<div class="f-sep"></div>
<div class="notices">
  <div>State Realty Licensing Board Mandated Disclosure Notices</div>
  <div class="u">State Realty Licensing Board Information About Brokerage Services</div>
  <div class="u">State Realty Licensing Board Consumer Protection Notice</div>
</div>

<div class="copyright">
  <p>Copyright © 2018 VTMB. All Right Reserved.</p>
  <div class="socials"><i></i><i style="background:#d94a3c"></i><i style="background:#2a7bbf"></i></div>
</div>

</body>
</html>
```